Project Overview:
We are looking to create a website for a monthly subscription IPTV service in WordPress. The website should provide a seamless user experience for customers to sign up for the service and manage their account information. We need the following pages: Home Page, Product Page, Sign-Up Page, and Account Information Page.

Home Page:
The Home Page design should be simple and clean, with a dark theme and minimalistic design elements. We would like to include graphics of popular movie shows displayed on multiple devices. The page should highlight the key benefits and features of our service and provide a clear call-to-action for visitors to sign up.

Product Page:
The Product Page should provide detailed information about our subscription tiers and pricing plans. It should highlight the key features of each plan and provide a clear comparison between them. The page should also include a call-to-action button for visitors to sign up.

Sign-Up Page:
The Sign-Up Page is the conversion page where members will sign up for the service. It should collect the following information: Name, Phone Number, Email, Password, and Payment Information. The design should be simple, intuitive, and easy to use. It should highlight the benefits of our service and provide a clear call-to-action for visitors to sign up.

Account Information Page:
The Account Information Page should allow members to view and manage their account details. It should include the following information: Profile Image, Contact Details, Password Management, Payment Information Management, and Membership Expiration Date. The design should be user-friendly, intuitive, and easy to navigate.

Goals: The primary goal of the website is to provide an easy-to-use portal for customers to sign up for the service and manage their account information. The website should be user-friendly and visually appealing to attract potential customers.

Scope: The scope of the project includes designing a home page, a sign-up page, an account information page, and a payment information page. The website should be designed to be responsive and accessible on desktop and mobile devices.

Design Preferences: The design should be clean, modern, and visually appealing. The use of a color palette that is consistent with the brand identity is recommended. The website should be easy to navigate and provide a clear call-to-action for users to sign up for the service.

FYI: The subscription service I am designing a website for is related to an IPTV service. IPTV stands for Internet Protocol Television, which is a digital television broadcasting protocol that uses the internet to deliver TV programs and videos to viewers. The website will allow customers to sign up for the IPTV service and access their account information such as user name and password, membership tier, name, and payment details. Please let me know if you have any further questions, and I would be happy to provide more details. Thank you!

Dear Designers,

Thank you for your participation in our project. After reviewing the designs received so far, we have decided to update the brief to better reflect our needs and preferences. We apologize for any confusion this may cause, but we believe that these changes will result in better design submissions and a more successful project overall.

The updated brief is as follows:

We are looking to create a website for WordPress.

Also, here is the updated Brief.

Project Title: WordPress Website Design for Monthly Subscription IPTV Service

Project Overview:
We are looking to create a website for a monthly subscription IPTV service. The website should provide a seamless user experience for customers to sign up for the service and manage their account information. We need the following pages: Home Page, Product Page, Sign-Up Page, and Account Information Page.

Home Page:

Product Page:

Sign-Up Page:

Account Information Page:

Design Preferences:
We prefer a dark theme with minimalistic design elements and hits of our logo colors. The website should be easy to use and navigate, with clear calls-to-action and simple, intuitive forms. The design should be optimized for mobile devices and load quickly.

We hope that these updates provide you with a clearer understanding of our requirements and preferences. Please let us know if you have any questions or concerns. We look forward to seeing your revised designs.

Thank you again for your participation.
We will guarantee this project as soon as we see something we like that meets the updated requirements.

The website's target audience is individuals who are interested in subscribing to the monthly service.

4 page

• One item for sale and a client profile section.

```html
<!DOCTYPE html>
<html lang="en">
<head>
<meta charset="utf-8">
<title>VIEWRA – IPTV Subscription Service</title>
<link rel="stylesheet" href="https://fonts.googleapis.com/css2?family=Montserrat:wght@400;500;600;700;800&family=Open+Sans:wght@400;600&display=swap">
<style>
:root{
  --red:#e3161b;
  --ink:#1d1d1f;
  --text:#4a4a4a;
  --muted:#6b6b6b;
  --navy:#1b242d;
  --slate:#2b2b36;
  --footer:#1a1a1d;
  --light:#f5f4f5;
  --pill:#f1f1f2;
  --white:#ffffff;
  --line:#e6e6e8;
}
*{box-sizing:border-box;margin:0;padding:0}
html,body{width:1200px;height:4498px;overflow:hidden}
body{position:relative;background:var(--white);font-family:"Open Sans",Arial,sans-serif;color:var(--text)}
.abs{position:absolute}
.btn{position:absolute;display:flex;align-items:center;justify-content:center;background:var(--red);color:var(--white);font-family:"Montserrat",Arial,sans-serif;font-weight:700;font-size:15px;text-transform:uppercase;border-radius:6px;letter-spacing:.2px;text-decoration:none}
.rule{position:absolute;width:30px;height:3px;background:var(--red)}
.brand{font-family:"Montserrat",Arial,sans-serif;font-weight:800;color:var(--red);letter-spacing:1px}

/* header */
.site-header{position:absolute;left:0;top:0;width:1200px;height:90px;background:var(--white)}
.site-header .brand{position:absolute;left:133px;top:22px;font-size:34px}
.nav a{position:absolute;top:35px;font-family:"Montserrat",Arial,sans-serif;font-weight:500;font-size:14px;color:var(--ink);text-decoration:none}
.nav a.active{color:var(--red)}
.nav a.active::after{content:"";position:absolute;left:0;right:0;top:27px;height:2px;background:var(--red)}

/* hero */
.hero{position:absolute;left:0;top:90px;width:1200px;height:609px}
.hero-photo{position:absolute;inset:0;background:radial-gradient(ellipse at 30% 40%,#4a5766 0%,#27313c 45%,#0d1218 100%)}
.hero-title{position:absolute;left:143px;top:300px;font-family:"Montserrat",Arial,sans-serif;font-weight:800;font-size:35px;line-height:42px;color:var(--white);text-transform:uppercase}
.dots{position:absolute;left:563px;top:563px;display:flex;gap:8px}
.dots i{width:8px;height:8px;border-radius:50%;background:var(--white)}
.dots i.on{background:var(--red)}

/* benefits */
.section-title{position:absolute;left:0;width:1200px;text-align:center;font-family:"Montserrat",Arial,sans-serif;font-weight:700;font-size:18px;color:var(--ink);text-transform:uppercase}
.card{position:absolute;width:304px;background:var(--white);border-radius:10px;box-shadow:0 4px 22px rgba(0,0,0,.07);text-align:center;padding:30px 44px 0}
.card svg{display:block;margin:0 auto 16px}
.card h3{font-family:"Montserrat",Arial,sans-serif;font-weight:600;font-size:14.5px;color:var(--ink);margin-bottom:14px}
.card p{font-size:12px;line-height:19px;color:var(--muted)}

/* dark feature bands */
.band{position:absolute;left:0;width:1200px}
.band-title{position:absolute;left:131px;font-family:"Montserrat",Arial,sans-serif;font-weight:700;font-size:19px;line-height:28px;color:var(--white);text-transform:uppercase}
.band-copy{position:absolute;left:131px;width:300px;font-size:14px;line-height:22.5px;color:#e3e5e8}

/* packages */
.packages{position:absolute;left:0;top:1967px;width:1200px;height:706px;background:var(--light)}
.plan{position:absolute;top:147px;width:222px;height:498px;background:var(--white);border-radius:8px;box-shadow:0 3px 16px rgba(0,0,0,.05);text-align:center;padding-top:28px}
.plan .period{font-family:"Montserrat",Arial,sans-serif;font-weight:500;font-size:15.5px;color:var(--ink)}
.plan .price{font-family:"Montserrat",Arial,sans-serif;font-weight:700;font-size:25px;color:var(--red);margin-top:6px}
.plan ul{list-style:none;margin:18px 16px 0;text-align:left}
.plan li{position:relative;font-size:11.5px;line-height:18px;color:#555;padding:8px 8px 8px 34px;border-radius:6px;margin-bottom:4px}
.plan li:nth-child(even){background:var(--pill)}
.plan li::before{content:"";position:absolute;left:14px;top:12px;width:9px;height:5px;border-left:1.5px solid #777;border-bottom:1.5px solid #777;transform:rotate(-45deg)}
.plan .btn{left:65px;top:438px;width:92px;height:36px;font-size:13px}

/* key features */
.feature{position:absolute;top:2821px;width:254px;height:297px;text-align:center;padding:40px 30px 0}
.feature svg{display:block;margin:0 auto 22px}
.feature h3{font-family:"Montserrat",Arial,sans-serif;font-weight:600;font-size:14.5px;color:var(--ink);margin-bottom:14px}
.feature p{font-size:12px;line-height:19px;color:var(--muted)}
.divider{position:absolute;top:2821px;width:1px;height:297px;background:var(--line)}

/* statement */
.statement{position:absolute;left:0;top:3790px;width:1200px;text-align:center;font-family:"Montserrat",Arial,sans-serif;font-weight:400;font-size:28px;line-height:38.5px;color:var(--ink)}

/* footer */
.site-footer{position:absolute;left:0;top:4076px;width:1200px;height:422px}
.footer-bg{position:absolute;inset:0}
.site-footer .brand{position:absolute;left:175px;top:170px;font-size:34px}
.f-col h4{position:absolute;font-family:"Montserrat",Arial,sans-serif;font-weight:700;font-size:13px;color:var(--white);text-transform:uppercase;padding-bottom:10px;border-bottom:2px solid var(--white)}
.f-item{position:absolute;display:flex;align-items:flex-start;gap:12px;font-size:11.5px;line-height:15px;color:#e8e8e8}
.f-item .ico{flex:none;width:22px;height:22px;border-radius:50%;background:var(--red);display:flex;align-items:center;justify-content:center}
.f-links{position:absolute;font-size:11.5px;line-height:19px;color:#e8e8e8}
.copyright{position:absolute;left:0;top:4447px;width:1200px;text-align:center;font-size:11px;color:#d9d9d9}
</style>
</head>
<body>

<header class="site-header">
  <div class="brand">VIEWRA</div>
  <nav class="nav">
    <a class="active" href="#" style="left:489px">HOME</a>
    <a href="#" style="left:567px">ABOUT US</a>
    <a href="#" style="left:675px">IPTV SUBSCRIPTION</a>
    <a href="#" style="left:847px">CONTACT US</a>
  </nav>
  <a class="btn" href="#" style="left:966px;top:24px;width:103px;height:39px;font-size:14px">SIGNUP</a>
</header>

<section class="hero">
  <div class="hero-photo" role="img" aria-label="Wall of glowing TV screens with a hand holding a remote control"></div>
  <h1 class="hero-title"># 1 OF THE BEST IPTV<br>SUBSCRIPTION SERVICE<br>PROVIDER</h1>
  <a class="btn" href="#" style="left:145px;top:453px;width:258px;height:47px;font-size:14.5px">BUY SUBSCRIPTION NOW</a>
  <a class="btn" href="#" style="left:419px;top:453px;width:156px;height:47px;font-size:14.5px">CONTACT US</a>
  <div class="dots"><i></i><i></i><i class="on"></i><i></i><i></i></div>
</section>

<section class="benefits">
  <h2 class="section-title" style="top:751px">VIEWRA IPTV SERVICE</h2>
  <div class="rule" style="left:585px;top:797px"></div>

  <div class="card" style="left:131px;top:847px;height:231px">
    <svg width="52" height="52" viewBox="0 0 52 52" fill="none" stroke="var(--red)" stroke-width="1.6"><rect x="4" y="4" width="44" height="12" rx="2"/><circle cx="12" cy="10" r="2"/><circle cx="20" cy="10" r="2"/><circle cx="28" cy="10" r="2"/><circle cx="36" cy="10" r="2"/><path d="M22 48V24a3 3 0 0 1 6 0v10l8 2a4 4 0 0 1 3 4v8"/></svg>
    <h3>Instant Activation!</h3>
    <p>After placing your order, all features will be fully accessible in just a few moments.</p>
  </div>
  <div class="card" style="left:449px;top:847px;height:231px">
    <svg width="60" height="56" viewBox="0 0 60 56" fill="none" stroke="var(--red)" stroke-width="1.6"><circle cx="30" cy="28" r="9"/><path d="M26 28l3 3 5-6"/><circle cx="30" cy="5" r="4"/><circle cx="30" cy="51" r="4"/><circle cx="7" cy="16" r="4"/><circle cx="53" cy="16" r="4"/><circle cx="7" cy="40" r="4"/><circle cx="53" cy="40" r="4"/><path d="M30 9v10M30 37v10M11 18l11 6M49 18l-11 6M11 38l11-6M49 38l-11-6"/></svg>
    <h3>Easy Setup</h3>
    <p>An internet connection is the only requirement for this setup; there are no dishes or antennas involved.</p>
  </div>
  <div class="card" style="left:765px;top:847px;height:231px">
    <svg width="30" height="54" viewBox="0 0 30 54" fill="none" stroke="var(--red)" stroke-width="1.6"><rect x="4" y="2" width="22" height="50" rx="5"/><circle cx="15" cy="11" r="3"/><path d="M9 20h12M9 26h4M17 26h4M9 32h4M17 32h4M9 38h4M17 38h4"/></svg>
    <h3>20,000+ TV Channels</h3>
    <p>Never miss a single episode of your favorite TV show or sporting event with complete access to over 20,000</p>
  </div>

  <div class="card" style="left:131px;top:1094px;height:263px">
    <svg width="56" height="52" viewBox="0 0 56 52" fill="none" stroke="var(--red)" stroke-width="1.6"><rect x="2" y="4" width="44" height="30" rx="2"/><path d="M18 34v8M12 42h18"/><rect x="36" y="20" width="18" height="28" rx="2"/><path d="M42 44h6"/></svg>
    <h3>Multiple Device and Format</h3>
    <p>Our IPTV service is compatible with all devices and apps, allowing you to order it through your preferred device or app.</p>
  </div>
  <div class="card" style="left:449px;top:1094px;height:263px">
    <svg width="52" height="52" viewBox="0 0 52 52" fill="none" stroke="var(--red)" stroke-width="1.6"><path d="M10 28v-6a16 16 0 0 1 32 0v6"/><rect x="6" y="26" width="8" height="14" rx="3"/><rect x="38" y="26" width="8" height="14" rx="3"/><path d="M42 40c0 6-6 8-12 8h-4"/></svg>
    <h3>Fast Support</h3>
    <p>We offer various contact methods for your convenience, enabling you to reach us anytime.</p>
  </div>
  <div class="card" style="left:765px;top:1094px;height:263px">
    <svg width="52" height="52" viewBox="0 0 52 52" fill="none" stroke="var(--red)" stroke-width="1.8"><path d="M44 22A19 19 0 0 0 10 14"/><path d="M10 6v8h8"/><path d="M8 30a19 19 0 0 0 34 8"/><path d="M42 46v-8h-8"/></svg>
    <h3>Auto and free update</h3>
    <p>Our service is frequently updated with new TV channels and VODs, and subscribing to it means you'll receive all future updates at no additional cost during your subscription period.</p>
  </div>
</section>

<section class="band" style="top:1401px;height:566px">
  <svg class="abs" width="1200" height="566" viewBox="0 0 1200 566" style="left:0;top:0">
    <rect width="1200" height="566" fill="var(--navy)"/>
  </svg>
  <div class="abs" role="img" aria-label="Child pointing at a TV screen showing a streaming app" style="left:472px;top:0;width:728px;height:566px;background:linear-gradient(120deg,#2d4a72 0%,#5a6f8c 35%,#8a5a3a 75%,#b9874d 100%);clip-path:polygon(0 49px,100% 0,100% 460px,0 526px)"></div>
  <h2 class="band-title" style="top:103px">LIVE SPORT AND TV-SHOWS<br>WITH OUR IPTV SUBSCRIPTION<br>SERVICE</h2>
  <div class="rule" style="left:131px;top:189px"></div>
  <p class="band-copy" style="top:222px">VIEWRA IPTV Provider offers a more flexible video experience for subscribers in comparison to traditional cable TV. With our service, you'll have access to a wide selection of popular national and international channels all in one place, eliminating the need to subscribe to multiple streaming services.</p>
  <a class="btn" href="#" style="left:136px;top:439px;width:157px;height:46px">CONTACT US</a>
</section>

<section class="packages">
  <h2 class="section-title" style="top:44px">IPTV SUBSCRIPTION PACKAGES</h2>
  <div class="rule" style="left:585px;top:89px"></div>

  <div class="plan" style="left:131px">
    <div class="period">1 MONTH</div><div class="price">$9.99</div>
    <ul><li>7-Days Trial Money<br>back guarantee</li><li>Instant Activation!</li><li>Free update<br>(TVs and VODs)</li><li>Over 20000 Premium<br>Channels</li><li>Compatible with<br>All Devices And Apps</li><li>24/7 Online support</li></ul>
    <a class="btn" href="#">SIGNUP</a>
  </div>
  <div class="plan" style="left:372px">
    <div class="period">3 MONTHS</div><div class="price">$19.99</div>
    <ul><li>7-Days Trial Money<br>back guarantee</li><li>Instant Activation!</li><li>Free update<br>(TVs and VODs)</li><li>Over 20000 Premium<br>Channels</li><li>Compatible with<br>All Devices And Apps</li><li>24/7 Online support</li></ul>
    <a class="btn" href="#">SIGNUP</a>
  </div>
  <div class="plan" style="left:611px">
    <div class="period">6 MONTHS</div><div class="price">$29.99</div>
    <ul><li>7-Days Trial Money<br>back guarantee</li><li>Instant Activation!</li><li>Free update<br>(TVs and VODs)</li><li>Over 20000 Premium<br>Channels</li><li>Compatible with<br>All Devices And Apps</li><li>24/7 Online support</li></ul>
    <a class="btn" href="#">SIGNUP</a>
  </div>
  <div class="plan" style="left:849px">
    <div class="period">12 MONTHS</div><div class="price">$49.99</div>
    <ul><li>7-Days Trial Money<br>back guarantee</li><li>Instant Activation!</li><li>Free update<br>(TVs and VODs)</li><li>Over 20000 Premium<br>Channels</li><li>Compatible with<br>All Devices And Apps</li><li>24/7 Online support</li></ul>
    <a class="btn" href="#">SIGNUP</a>
  </div>
</section>

<section class="key-features">
  <h2 class="section-title" style="top:2728px">KEY IPTV FEATURES</h2>
  <div class="rule" style="left:585px;top:2773px"></div>

  <div class="feature" style="left:103px">
    <svg width="52" height="52" viewBox="0 0 52 52" fill="none" stroke="var(--red)" stroke-width="1.6"><rect x="4" y="10" width="44" height="30" rx="2"/><path d="M18 40v6M34 40v6M14 46h24M20 4l6 6 6-6"/><path d="M22 19v12l10-6z"/></svg>
    <h3>Live TV Channels</h3>
    <p>We are not just an adult IPTV subscription service provider, but we also offer over 15,000 live TV channels from all around the world.</p>
  </div>
  <div class="divider" style="left:349px"></div>
  <div class="feature" style="left:352px">
    <svg width="52" height="52" viewBox="0 0 52 52" fill="none" stroke="var(--red)" stroke-width="1.6"><rect x="4" y="6" width="44" height="40" rx="2"/><path d="M12 6v40M40 6v40M4 16h8M4 26h8M4 36h8M40 16h8M40 26h8M40 36h8"/><path d="M22 19v14l10-7z"/></svg>
    <h3>VOD TV-series</h3>
    <p>Our IPTV service's key feature is the vast number of TV series available, with over 20,000 options to choose from. By purchasing a subscription from us</p>
  </div>
  <div class="divider" style="left:603px"></div>
  <div class="feature" style="left:604px">
    <svg width="52" height="52" viewBox="0 0 52 52" fill="none" stroke="var(--red)" stroke-width="1.6"><circle cx="26" cy="26" r="22"/><path d="M8 14c10 4 26 4 36 0M8 38c10-4 26-4 36 0M26 4c-8 10-8 34 0 44M26 4c8 10 8 34 0 44"/></svg>
    <h3>Live Sports Channels</h3>
    <p>At our IPTV subscription service, we prioritize the satisfaction of our users, which is why we provide all the major sports channels to ensure they never miss a live sports event.</p>
  </div>
  <div class="divider" style="left:854px"></div>
  <div class="feature" style="left:846px">
    <svg width="52" height="52" viewBox="0 0 52 52" fill="none" stroke="var(--red)" stroke-width="1.6"><circle cx="26" cy="24" r="12"/><path d="M10 26v-4a16 16 0 0 1 32 0v4"/><rect x="6" y="22" width="7" height="12" rx="3"/><rect x="39" y="22" width="7" height="12" rx="3"/><path d="M42 34c0 8-6 10-12 10M14 48c2-6 6-8 12-8s10 2 12 8"/></svg>
    <h3>24/7 Live Support</h3>
    <p>Our support team of expertly trained professionals is available 24/7 to assist you with any technical or billing-related issues you may encounter.</p>
  </div>
</section>

<section class="band" style="top:3153px;height:565px">
  <svg class="abs" width="1200" height="565" viewBox="0 0 1200 565" style="left:0;top:0">
    <polygon points="0,0 1200,45 1200,500 0,565" fill="var(--slate)"/>
  </svg>
  <div class="abs" role="img" aria-label="Person on a sofa pointing a remote at a TV showing a streaming app" style="left:524px;top:0;width:676px;height:565px;background:linear-gradient(110deg,#2b2b36 0%,#3c4656 30%,#6b7a88 60%,#4a4f5a 100%);clip-path:polygon(0 20px,100% 45px,100% 500px,0 535px)"></div>
  <h2 class="band-title" style="top:87px">WE PROVIDE BEST IPTV SERVICE<br>AROUND THE WORLD</h2>
  <div class="rule" style="left:131px;top:159px"></div>
  <p class="band-copy" style="top:203px;width:358px">Lorem ipsum dolor sit amet, consectetur adipiscing elit, sed do eiusmod tempor incididunt ut labore et dolore magna aliqua. Ut enim ad minim veniam, quis nostrud exercitation ullamco laboris nisi ut aliquip ex ea commodo consequat. Duis aute irure dolor in reprehenderit in voluptate velit esse cillum dolore eu fugiat nulla pariatur. Excepteur sint occaecat cupidatat non proident, sunt in culpa qui officia deserunt mollit anim id est laborum</p>
  <a class="btn" href="#" style="left:136px;top:434px;width:157px;height:46px">READ MORE</a>
</section>

<section>
  <p class="statement">The VIEWRA team has several years of<br>experience, we use the latest technologies<br>and top servers to provide you the<br>best quality IPTV service.</p>
  <a class="btn" href="#" style="left:522px;top:3966px;width:159px;height:47px">CONTACT US</a>
</section>

<footer class="site-footer">
  <svg class="footer-bg" width="1200" height="422" viewBox="0 0 1200 422"><polygon points="0,0 1200,65 1200,422 0,422" fill="var(--footer)"/></svg>
  <div class="brand">VIEWRA</div>

  <div class="f-col">
    <h4 style="left:404px;top:96px;width:193px">CONTACT US</h4>
    <div class="f-item" style="left:404px;top:148px">
      <span class="ico"><svg width="10" height="12" viewBox="0 0 10 12"><path d="M5 0a4 4 0 0 1 4 4c0 3-4 8-4 8S1 7 1 4a4 4 0 0 1 4-4z" fill="#fff"/><circle cx="5" cy="4" r="1.5" fill="var(--red)"/></svg></span>
      <span>48 Harbourview Rd, Maple Bay,<br>ON K2P 4R1, Canada</span>
    </div>
    <div class="f-item" style="left:404px;top:198px">
      <span class="ico"><svg width="11" height="11" viewBox="0 0 11 11"><path d="M2 0l2 3-1 1.5a7 7 0 0 0 3.5 3.5L8 7l3 2-1 2C5 11 0 6 0 1z" fill="#fff"/></svg></span>
      <span>Call Us<br>+1 555 014 2290</span>
    </div>
    <div class="f-item" style="left:404px;top:248px">
      <span class="ico"><svg width="12" height="9" viewBox="0 0 12 9"><rect width="12" height="9" rx="1" fill="#fff"/><path d="M0 1l6 4 6-4" stroke="var(--red)" fill="none"/></svg></span>
      <span>E mail Us<br>info@viewra.com</span>
    </div>

    <h4 style="left:716px;top:96px;width:105px">MENU</h4>
    <div class="f-links" style="left:716px;top:143px">Home<br>About us<br>IPTV SUBSCRIPTION<br>Contact Us</div>

    <h4 style="left:963px;top:96px;width:106px">FOLLOW US</h4>
    <div class="f-item" style="left:963px;top:146px"><span class="ico"></span><span>Like us on<br>FRIENDWALL</span></div>
    <div class="f-item" style="left:963px;top:196px"><span class="ico"></span><span>Follow us on<br>CHIRPLINE</span></div>
    <div class="f-item" style="left:963px;top:246px"><span class="ico"></span><span>Follow us on<br>WORKLINK</span></div>
  </div>

  <div class="abs" style="left:131px;top:330px;width:938px;height:1px;background:#d0d0d0"></div>
</footer>
<div class="copyright">Copyright © 2023 All Rights Reserved</div>

</body>
</html>
```